Nivel Crest - Powerpoint Templates

We are a consultancy to help builders to optimize their planning in order to save building costs. For that reason we need templates for teasers and presentations where we offer our services, show our team and their capacities and present workflows, organization charts, price lists etc.

```html
<!DOCTYPE html>
<html lang="en">
<head>
<meta charset="utf-8">
<title>Nivel Crest – Presentation Templates</title>
<link href="https://fonts.googleapis.com/css2?family=Audiowide&family=Lato:wght@400;700&display=swap" rel="stylesheet">
<style>
:root{
  --page:#1f1f1f;
  --white:#ffffff;
  --ink:#3a3a40;
  --ink-dark:#2e2e33;
  --text:#3d3d42;
  --gold:#c08a36;
  --gold-band:linear-gradient(90deg,#b57a2c 0%,#d6aa52 55%,#e3bd64 75%,#c08a38 100%);
  --dark-band:linear-gradient(90deg,#3a3a40 0%,#4e4e55 50%,#9a9aa0 80%,#d9d9dc 100%);
  --dark-foot:linear-gradient(90deg,#d9d9dc 0%,#6a6a70 35%,#3a3a40 70%,#3a3a40 100%);
  --gold-foot:linear-gradient(90deg,#c79042 0%,#e3bd64 45%,#c08a38 100%);
}
*{box-sizing:border-box;margin:0;padding:0}
html,body{width:1200px;height:4172px;overflow:hidden;background:var(--page)}
body{position:relative;font-family:'Lato',sans-serif;color:var(--text)}
.slide{position:absolute;left:62px;width:1096px;height:617px;background:var(--white);overflow:hidden}
.slide.soft{background:linear-gradient(180deg,#ffffff 0%,#f1f1f3 100%)}
.display{font-family:'Audiowide',sans-serif;text-transform:uppercase;letter-spacing:2px}

.band{position:absolute;top:0;left:0;width:1040px;height:64px;clip-path:polygon(0 0,100% 0,calc(100% - 52px) 100%,0 100%);display:flex;align-items:center;padding-left:53px}
.band.gold{background:var(--gold-band)}
.band.dark{background:var(--dark-band)}
.band h2{font-family:'Audiowide',sans-serif;font-weight:400;font-size:29px;color:var(--white);letter-spacing:3px;text-transform:uppercase}

.brand-mini{position:absolute;left:53px;bottom:16px;height:34px;display:flex;align-items:center}
.brand-mini .name{font-family:'Audiowide',sans-serif;font-size:30px;color:var(--gold);letter-spacing:1px;line-height:1;display:flex;align-items:center;gap:10px}
.brand-mini .name i{display:block;width:26px;height:26px;background:var(--ink)}
.foot{position:absolute;right:0;bottom:0;width:643px;height:65px;clip-path:polygon(52px 0,100% 0,100% 100%,0 100%);display:flex;align-items:center}
.foot.gold{background:var(--gold-foot)}
.foot.dark{background:var(--dark-foot)}
.foot .ico{width:36px;height:36px;border-radius:50%;background:var(--ink-dark);display:flex;align-items:center;justify-content:center;flex:none}
.foot .mail{position:absolute;left:60px;top:15px;display:flex;align-items:center;gap:16px;font-size:19px;color:var(--white)}
.foot .phone{position:absolute;left:306px;top:15px;display:flex;align-items:center;gap:12px;font-size:19px;color:var(--white)}
.foot .num{position:absolute;left:568px;top:15px;width:36px;height:36px;border-radius:50%;background:var(--ink-dark);color:var(--white);font-family:'Audiowide',sans-serif;font-size:15px;display:flex;align-items:center;justify-content:center}

.bullets{list-style:none;position:absolute}
.bullets li{position:relative;padding-left:26px;font-size:19.5px;line-height:34px;margin-bottom:9px}
.bullets li svg{position:absolute;left:0;top:10px}

.sketch{position:absolute;left:0;right:0;top:120px;bottom:0;background:linear-gradient(180deg,rgba(240,240,242,0) 0%,#ececef 55%,#e6e6ea 100%)}

.s1-grey{position:absolute;inset:0;background:linear-gradient(160deg,#e6e6e8,#bdbdc1);clip-path:polygon(0 0,267px 0,267px 160px,0 560px)}
.s1-gold{position:absolute;inset:0;background:linear-gradient(160deg,#d9a94f 0%,#f0d27a 45%,#c28a38 100%);clip-path:polygon(830px 89px,1096px 300px,1096px 617px,830px 617px)}
.s1-mark{position:absolute;left:348px;top:150px;width:400px;text-align:center;font-family:'Audiowide',sans-serif;font-size:44px;color:var(--ink);letter-spacing:2px;display:flex;flex-direction:column;align-items:center;gap:18px}
.s1-mark i{display:block;width:70px;height:70px;background:var(--gold)}
.welcome{position:absolute;left:0;width:1096px;text-align:center}

.house{position:absolute;width:267px;clip-path:polygon(50% 0,100% 28%,100% 100%,0 100%,0 28%)}
.card{height:256px;color:var(--white);text-align:center;padding-top:138px}
.card.dark{background:var(--ink)}
.card.gold{background:var(--gold)}
.card h3{font-family:'Audiowide',sans-serif;font-weight:400;font-size:15px;letter-spacing:1px;text-transform:uppercase}
.card p{font-size:11.5px;line-height:24px;margin:6px 20px 0}
.card svg{position:absolute;left:103px;top:42px}

.member{height:256px;padding:9px}
.member.dark{background:var(--ink)}
.member.gold{background:var(--gold)}
.member .photo{width:100%;height:100%;clip-path:polygon(50% 0,100% 28%,100% 100%,0 100%,0 28%)}
.member-name{position:absolute;width:267px;text-align:center}
.member-name h3{font-family:'Audiowide',sans-serif;font-weight:400;font-size:23px;color:var(--ink);letter-spacing:2px;text-transform:uppercase}
.member-name p{font-size:13px;color:var(--ink);margin-top:12px;text-transform:uppercase}

.contact{position:absolute;left:60px}
.contact .row{position:absolute;left:0;display:flex;gap:8px;width:500px}
.contact .pin{width:36px;height:36px;border-radius:50%;background:var(--ink);display:flex;align-items:center;justify-content:center;flex:none}
.contact h4{font-family:'Audiowide',sans-serif;font-weight:400;font-size:16px;color:var(--ink);text-transform:uppercase;letter-spacing:1px}
.contact .val{font-size:20px;color:var(--ink-dark);margin-top:8px}
.thanks{position:absolute;left:53px;font-family:'Audiowide',sans-serif;font-size:41px;color:var(--ink);letter-spacing:3px;line-height:64px;text-transform:uppercase}
.big-mark{position:absolute;left:660px;top:240px;width:400px;text-align:center;font-family:'Audiowide',sans-serif;font-size:46px;color:var(--ink);display:flex;flex-direction:column;align-items:center;gap:18px}
.big-mark i{display:block;width:80px;height:80px;background:var(--gold)}
</style>
</head>
<body>

<section class="slide" style="top:57px">
  <div class="s1-grey"></div>
  <div class="s1-gold"></div>
  <div class="s1-mark"><i></i>NIVEL CREST</div>
  <div class="welcome display" style="top:372px;font-size:29px;color:var(--gold)">Welcome to</div>
  <div class="welcome display" style="top:420px;font-size:50px;color:var(--ink)">Nivel Crest</div>
  <div class="welcome" style="top:494px;font-size:18px;color:var(--ink);letter-spacing:2px">Smarter planning, lower costs</div>
  <svg style="position:absolute;left:454px;top:535px" width="190" height="38" aria-hidden="true">
    <g fill="none" stroke="#c08a36" stroke-width="2.5">
      <circle cx="19" cy="19" r="16"/><circle cx="70" cy="19" r="16"/><circle cx="120" cy="19" r="16"/><circle cx="171" cy="19" r="16"/>
    </g>
  </svg>
</section>

<section class="slide" style="top:724px">
  <div class="band gold"><h2>About Nivel Crest</h2></div>
  <ul class="bullets" style="left:53px;top:82px;width:570px">
    <li><svg width="16" height="14"><path d="M1 7h12M8 2l5 5-5 5" stroke="#c08a36" stroke-width="2.5" fill="none"/></svg>Temporibus autem quibusdam et aut officiis debitis aut rerum saepe eveniet ut et voluptates repudiandae sint et molestiae non tempore, cum soluta recusandae.</li>
    <li><svg width="16" height="14"><path d="M1 7h12M8 2l5 5-5 5" stroke="#c08a36" stroke-width="2.5" fill="none"/></svg>Nam libero tempore, cum soluta nobis est eligendi optio c impedit quo minus id quod maxime placeat facere possimus, voluptas assumenda est, omnis dolor repellendus.</li>
    <li><svg width="16" height="14"><path d="M1 7h12M8 2l5 5-5 5" stroke="#c08a36" stroke-width="2.5" fill="none"/></svg>At vero eos et accusamus et iusto odio dignissimos ducimus qui blanditiis praesentium voluptatum deleniti atque corrupti quos dolores et quas molestias excepturi.</li>
    <li><svg width="16" height="14"><path d="M1 7h12M8 2l5 5-5 5" stroke="#c08a36" stroke-width="2.5" fill="none"/></svg>Itaque earum rerum hic tenetur a sapiente delectus, ut aut reiciendis voluptatibus maiores alias consequatur aut perf erendis doloribus asperiores repellat.</li>
  </ul>
  <div style="position:absolute;left:645px;top:95px;width:420px;height:400px;background:var(--ink);transform:rotate(3deg)"></div>
  <div style="position:absolute;left:655px;top:88px;width:412px;height:400px;background:var(--gold);transform:rotate(-2deg)"></div>
  <div role="img" aria-label="Photo of two colleagues in a meeting at a glass table" style="position:absolute;left:660px;top:92px;width:398px;height:396px;background:linear-gradient(135deg,#dfe6ea 0%,#b9c2c6 45%,#6f6a60 80%,#3e3a36 100%)"></div>
  <div class="brand-mini"><div class="name"><i></i>NIVEL CREST</div></div>
  <div class="foot gold">
    <div class="mail"><span class="ico"><svg width="16" height="12"><rect x="1" y="1" width="14" height="10" fill="#fff"/><path d="M1 1l7 5 7-5" stroke="#2e2e33" fill="none"/></svg></span>info@nivelcrest.com</div>
    <div class="phone"><span class="ico"><svg width="16" height="16"><path d="M3 1l3 3-2 2c1 2 3 4 5 5l2-2 3 3-2 3C7 15 1 9 1 3z" fill="#fff"/></svg></span>+1 555 010 2040</div>
    <div class="num">2</div>
  </div>
</section>

<section class="slide" style="top:1394px">
  <div class="sketch"></div>
  <div class="band dark"><h2>We offer our services</h2></div>
  <p style="position:absolute;left:53px;top:90px;width:960px;font-size:19.5px;line-height:34px">Temporibus autem quibusdam et aut officiis debitis aut rerum necessitatibus saepe eveniet ut et voluptates repudiandae sint et molestiae non recusandae.</p>
  <div class="house card dark" style="left:53px;top:196px">
    <svg width="60" height="70" aria-hidden="true"><g fill="none" stroke="#fff" stroke-width="2.5"><circle cx="30" cy="20" r="11"/><path d="M8 66v-14c0-8 10-14 22-14s22 6 22 14v14z"/></g></svg>
    <h3>Temporibus autem</h3>
    <p>Temporibus autem quibusdam et aut officiis debitis aut rerum necessitatibus saepe eveniet ut et voluptates</p>
  </div>
  <div class="house card gold" style="left:414px;top:196px">
    <svg width="60" height="70" aria-hidden="true"><g fill="none" stroke="#fff" stroke-width="2.5"><rect x="8" y="8" width="40" height="58" rx="3"/><rect x="20" y="3" width="16" height="9"/><path d="M15 26l4 4 7-7M15 44l4 4 7-7M32 27h10M32 45h10"/></g></svg>
    <h3>Itaque earum rerum</h3>
    <p>Itaque earum rerum hic tenetur a sapiente delectus, ut aut reiciendis voluptatibus maiores alias consequatur</p>
  </div>
  <div class="house card dark" style="left:772px;top:196px">
    <svg width="60" height="70" aria-hidden="true"><g fill="none" stroke="#fff" stroke-width="2.5"><path d="M14 30a16 16 0 0 1 32 0z"/><path d="M8 30h44"/><path d="M10 42h40l-4 22H14z"/></g></svg>
    <h3>Nam libero tempore</h3>
    <p>Nam libero tempore, cum soluta nobis est eligendi optio cumque nihil impedit quo minus id quod maxime placeat</p>
  </div>
  <div class="brand-mini"><div class="name"><i></i>NIVEL CREST</div></div>
  <div class="foot dark">
    <div class="mail"><span class="ico"><svg width="16" height="12"><rect x="1" y="1" width="14" height="10" fill="#fff"/><path d="M1 1l7 5 7-5" stroke="#2e2e33" fill="none"/></svg></span>info@nivelcrest.com</div>
    <div class="phone"><span class="ico"><svg width="16" height="16"><path d="M3 1l3 3-2 2c1 2 3 4 5 5l2-2 3 3-2 3C7 15 1 9 1 3z" fill="#fff"/></svg></span>+1 555 010 2040</div>
    <div class="num">3</div>
  </div>
</section>

<section class="slide" style="top:2066px">
  <div class="band gold"><h2>Organization charts</h2></div>
  <svg style="position:absolute;left:40px;top:120px" width="600" height="390" font-family="Lato,sans-serif" font-size="11" fill="#3d3d42" aria-label="Bar chart of values per weekday">
    <g stroke="#e2e2e5" stroke-width="1">
      <line x1="40" y1="12" x2="590" y2="12"/><line x1="40" y1="69" x2="590" y2="69"/><line x1="40" y1="126" x2="590" y2="126"/><line x1="40" y1="183" x2="590" y2="183"/><line x1="40" y1="240" x2="590" y2="240"/><line x1="40" y1="297" x2="590" y2="297"/><line x1="40" y1="354" x2="590" y2="354"/>
      <line x1="40" y1="12" x2="40" y2="354"/><line x1="117" y1="12" x2="117" y2="354"/><line x1="193" y1="12" x2="193" y2="354"/><line x1="269" y1="12" x2="269" y2="354"/><line x1="345" y1="12" x2="345" y2="354"/><line x1="421" y1="12" x2="421" y2="354"/><line x1="497" y1="12" x2="497" y2="354"/><line x1="590" y1="12" x2="590" y2="354"/>
    </g>
    <g text-anchor="end"><text x="24" y="16">120</text><text x="24" y="73">100</text><text x="24" y="130">80</text><text x="24" y="187">60</text><text x="24" y="244">40</text><text x="24" y="301">20</text><text x="24" y="358">0</text></g>
    <g>
      <rect x="66" y="69" width="14" height="285" fill="#c08a36"/><rect x="88" y="97" width="14" height="257" fill="#3a3a40"/>
      <rect x="142" y="97" width="14" height="257" fill="#c08a36"/><rect x="164" y="126" width="14" height="228" fill="#3a3a40"/>
      <rect x="218" y="211" width="14" height="143" fill="#c08a36"/><rect x="240" y="69" width="14" height="285" fill="#3a3a40"/>
      <rect x="294" y="69" width="14" height="285" fill="#c08a36"/><rect x="316" y="183" width="14" height="171" fill="#3a3a40"/>
      <rect x="370" y="69" width="14" height="285" fill="#c08a36"/><rect x="392" y="97" width="14" height="257" fill="#3a3a40"/>
      <rect x="446" y="183" width="14" height="171" fill="#c08a36"/><rect x="468" y="140" width="14" height="214" fill="#3a3a40"/>
      <rect x="522" y="211" width="14" height="143" fill="#c08a36"/><rect x="544" y="69" width="14" height="285" fill="#3a3a40"/>
    </g>
    <g text-anchor="middle">
      <text x="73" y="63">100</text><text x="95" y="91">90</text><text x="149" y="91">90</text><text x="171" y="120">80</text>
      <text x="225" y="205">50</text><text x="247" y="63">100</text><text x="301" y="63">100</text><text x="323" y="177">60</text>
      <text x="377" y="63">100</text><text x="399" y="91">90</text><text x="453" y="177">60</text><text x="475" y="134">75</text>
      <text x="529" y="205">50</text><text x="551" y="63">100</text>
      <text x="84" y="374">Sun</text><text x="160" y="374">Mon</text><text x="236" y="374">Tue</text><text x="312" y="374">Wed</text><text x="388" y="374">Thu</text><text x="464" y="374">Fri</text><text x="540" y="374">Sat</text>
    </g>
  </svg>
  <ul class="bullets" style="left:659px;top:112px;width:410px">
    <li><svg width="16" height="14"><path d="M1 7h12M8 2l5 5-5 5" stroke="#c08a36" stroke-width="2.5" fill="none"/></svg>Temporibus autem quibusdam et aut officiis debitis aut rerum necessitatibus saepe eveniet ut et voluptates repudiand ae sint et molestiae non tempore, cum soluta recusandae.</li>
    <li><svg width="16" height="14"><path d="M1 7h12M8 2l5 5-5 5" stroke="#c08a36" stroke-width="2.5" fill="none"/></svg>Nam libero tempore, cum soluta nobis est eligendi optio cumque nihil impedit quo minus id quod maxime.</li>
    <li><svg width="16" height="14"><path d="M1 7h12M8 2l5 5-5 5" stroke="#c08a36" stroke-width="2.5" fill="none"/></svg>Itaque earum rerum hic tenetur a sapiente delectus, ut aut reiciendis voluptatibus doloribus asperiores repellat.</li>
  </ul>
  <div class="brand-mini"><div class="name"><i></i>NIVEL CREST</div></div>
  <div class="foot gold">
    <div class="mail"><span class="ico"><svg width="16" height="12"><rect x="1" y="1" width="14" height="10" fill="#fff"/><path d="M1 1l7 5 7-5" stroke="#2e2e33" fill="none"/></svg></span>info@nivelcrest.com</div>
    <div class="phone"><span class="ico"><svg width="16" height="16"><path d="M3 1l3 3-2 2c1 2 3 4 5 5l2-2 3 3-2 3C7 15 1 9 1 3z" fill="#fff"/></svg></span>+1 555 010 2040</div>
    <div class="num">4</div>
  </div>
</section>

<section class="slide" style="top:2749px">
  <div class="sketch"></div>
  <div class="band dark"><h2>Our team</h2></div>
  <div class="house member dark" style="left:53px;top:141px"><div class="photo" role="img" aria-label="Portrait of team member in a dark suit" style="background:linear-gradient(180deg,#b7cbd6 0%,#8fa6b3 55%,#2b2f3a 100%)"></div></div>
  <div class="house member gold" style="left:414px;top:141px"><div class="photo" role="img" aria-label="Portrait of team member in a light blue shirt" style="background:linear-gradient(180deg,#c9dde6 0%,#a9c6d4 55%,#6fb3d6 100%)"></div></div>
  <div class="house member dark" style="left:772px;top:141px"><div class="photo" role="img" aria-label="Portrait of team member in a white blouse" style="background:linear-gradient(180deg,#b7cbd6 0%,#98afbd 50%,#e8ecef 100%)"></div></div>
  <div class="member-name" style="left:53px;top:414px"><h3>Alan Merrit</h3><p>Temporibus</p></div>
  <div class="member-name" style="left:414px;top:414px"><h3>Tomas Vey</h3><p>Itaque earum</p></div>
  <div class="member-name" style="left:772px;top:414px"><h3>Lena Hart</h3><p>Necessitatibu</p></div>
  <div class="brand-mini"><div class="name"><i></i>NIVEL CREST</div></div>
  <div class="foot dark">
    <div class="mail"><span class="ico"><svg width="16" height="12"><rect x="1" y="1" width="14" height="10" fill="#fff"/><path d="M1 1l7 5 7-5" stroke="#2e2e33" fill="none"/></svg></span>info@nivelcrest.com</div>
    <div class="phone"><span class="ico"><svg width="16" height="16"><path d="M3 1l3 3-2 2c1 2 3 4 5 5l2-2 3 3-2 3C7 15 1 9 1 3z" fill="#fff"/></svg></span>+1 555 010 2040</div>
    <div class="num">5</div>
  </div>
</section>

<section class="slide soft" style="top:3431px">
  <div class="band gold"><h2>Get in touch with us</h2></div>
  <div class="contact">
    <div class="row" style="top:120px"><span class="pin"><svg width="14" height="18"><path d="M7 1a6 6 0 0 1 6 6c0 5-6 10-6 10S1 12 1 7a6 6 0 0 1 6-6z" fill="#fff"/><circle cx="7" cy="7" r="2.2" fill="#3a3a40"/></svg></span><div><h4>Address:</h4><div class="val">Nivel Crest, United States</div></div></div>
    <div class="row" style="top:216px"><span class="pin"><svg width="16" height="12"><rect x="1" y="1" width="14" height="10" fill="#fff"/><path d="M1 1l7 5 7-5" stroke="#3a3a40" fill="none"/></svg></span><div><h4>Email us:</h4><div class="val">info@nivelcrest.com</div></div></div>
    <div class="row" style="top:318px"><span class="pin"><svg width="16" height="16"><path d="M3 1l3 3-2 2c1 2 3 4 5 5l2-2 3 3-2 3C7 15 1 9 1 3z" fill="#fff"/></svg></span><div><h4>Phone number:</h4><div class="val">+1 555 010 2040</div></div></div>
  </div>
  <div class="thanks" style="top:432px">Thank you<br>Nivel Crest</div>
  <div class="big-mark"><i></i>NIVEL CREST</div>
</section>

</body>
</html>
```